Home Security Company Business Card

Looking for a eye catching business card that is non traditional and stands out but yet still looks professional. It should include all the pertinent information such as name, title, address, telephone, e-mail, website address should definitely stand out and then finally the logo.

Target Market(s)

Residential and Commercial accounts mostly upscale accounts

Industry/Entity Type

Security

Contact Information for Business Card

Name
Title
Address
Office #
Cell #
E-mail
Website

Font styles to use
Serif
Sans Serif

Requirements
Must have
• Logo, two sided color configuration
Nice to have
• You decide
Should not have
• There really aren't any.

```html
<!DOCTYPE html>
<html lang="en">
<head>
<meta charset="utf-8">
<title>Harborline Security Systems – Business Card</title>
<link rel="stylesheet" href="https://fonts.googleapis.com/css2?family=Source+Sans+3:ital,wght@0,400;0,600;1,400&family=Tinos&display=swap">
<style>
  :root {
    --stage: #3b3b3b;
    --paper: #fbfbfa;
    --crimson: #730d00;
    --gold: #d9a23a;
    --gold-soft: #c98a2a;
    --ink: #4a4a4a;
    --light: #f3ece6;
  }
  * { box-sizing: border-box; margin: 0; padding: 0; }
  html, body {
    width: 1200px; height: 750px; overflow: hidden;
    background: var(--stage);
  }
  .canvas { position: relative; width: 1200px; height: 750px; }
  .card {
    position: absolute; top: 228px; width: 461px; height: 262px;
    overflow: hidden;
  }
  .card-front { left: 124px; background: var(--paper); }
  .card-back { left: 618px; background: var(--crimson); }

  .brand-mark {
    position: absolute; left: 160px; top: 270px;
    width: 58px; height: 58px; border-radius: 50%;
    background: var(--gold);
  }
  .card-front .brand-mark { left: 36px; top: 42px; }
  .brand-name {
    position: absolute; left: 114px; top: 78px;
    font-family: "Tinos", serif; color: var(--crimson);
    line-height: 1;
  }
  .brand-name .title { display: block; font-size: 18px; letter-spacing: 0.2px; }
  .brand-name .sub { display: block; font-size: 9.4px; margin-top: 1px; letter-spacing: -0.1px; }

  .address {
    position: absolute; left: 114px; top: 121px;
    font-family: "Source Sans 3", sans-serif; font-size: 11px;
    line-height: 14px; color: var(--ink);
  }
  .contacts {
    position: absolute; left: 114px; top: 156px; list-style: none;
    font-family: "Source Sans 3", sans-serif; font-size: 11px; color: var(--ink);
  }
  .contacts li { display: flex; align-items: center; height: 17.6px; }
  .contacts svg { width: 11px; height: 11px; margin-right: 6px; fill: var(--crimson); }

  .person {
    position: absolute; right: 36px; top: 157px; text-align: right;
    font-family: "Source Sans 3", sans-serif;
  }
  .person .name { font-size: 16px; font-weight: 600; color: var(--crimson); line-height: 19px; }
  .person .role { font-size: 12px; color: var(--gold-soft); line-height: 15px; }

  .card-back .brand-mark { left: 201px; top: 74px; }
  .back-name {
    position: absolute; left: 0; right: 0; top: 146px; text-align: center;
    font-family: "Tinos", serif; font-size: 18px; color: var(--gold);
  }
  .back-web {
    position: absolute; left: 0; right: 0; top: 218px; text-align: center;
    font-family: "Source Sans 3", sans-serif; font-style: italic;
    font-size: 11px; letter-spacing: 3px; color: #f4e9e4;
  }
</style>
</head>
<body>
<main class="canvas">
  <section class="card card-front" aria-label="Business card front">
    <div class="brand-mark" aria-hidden="true"></div>
    <div class="brand-name">
      <span class="title">HARBORLINE</span>
      <span class="sub">SECURITY SYSTEMS INC.</span>
    </div>
    <p class="address">4120 Alder Court<br>Juneau, Alaska 99801</p>
    <ul class="contacts">
      <li><svg viewBox="0 0 12 12"><path d="M2.5 0.5l2 2.2-1 1.3c.6 1.4 1.6 2.5 3 3.2l1.3-1 2.2 2-1 2.3C5.2 12 0 6.8.3 1.5z"/></svg>555 214 7730</li>
      <li><svg viewBox="0 0 12 12"><path d="M3 0h6v12H3zM4 1.3v8.4h4V1.3zM5.4 10.3h1.2v1H5.4z" fill-rule="evenodd"/></svg>555 386 0192</li>
      <li><svg viewBox="0 0 12 12"><path d="M0 2.5h12v7H0zM0.8 3.2L6 6.6l5.2-3.4v-.1H.8z"/></svg>hello@harborline.com</li>
      <li><svg viewBox="0 0 12 12"><circle cx="6" cy="6" r="5.6"/><path d="M3 3.5c1 .3 1.4 1.2 2.3 1.3.6.6-.2 1.5.5 2.3.4.8-.3 1.6.2 2.2L5 9.7C4.6 8.6 3.4 7.7 3.6 6.4 3 5.5 2.4 4.6 3 3.5zM7.5 2.2c.8.3 1.8.8 2 1.8-.8.2-1.5-.4-2-1.8z" fill="#fff"/></svg>www.harborline.com</li>
    </ul>
    <div class="person">
      <p class="name">Daniel Reyes</p>
      <p class="role">CEO/Founder</p>
    </div>
  </section>

  <section class="card card-back" aria-label="Business card back">
    <div class="brand-mark" aria-hidden="true"></div>
    <p class="back-name">HARBORLINE</p>
    <p class="back-web">www.harborline.com</p>
  </section>
</main>
</body>
</html>
```